Website for an electrical contractor :)

We are after a web site which can show pictures of our jobs and our capability in a professional, creative and easily understood way.

----- Brightvale Electrical ------

We really want a visually good looking website with three sections

Section one:
'Completed projects'
We have a few pictures of jobs which we've completed and would like to show off with a brief description. (see uploads)

Section two:
'Our capabilities'
Just a list of what services we offer

Section three:
We would like a 'contact us' section which people can send us a short msg and upload a file for plans to be able to send to us. We would need their name, phone number and email details. We would also need a short privacy policy saying 'we do not disclose information to third parties'.
We also want to display our contact number and postal address

Good luck :)

Target Market(s)

Adults 25 years+
Business owners
Builders
Real estate agents

Industry/Entity Type

Electrical

Colors

Designer to choose colors to be used in the design.

Requirements
Must have
• Visually appealing
Easy to understand
In the 'Completed projects' section, must have a list for each project we do i can upload pictures for it.

```html
<!DOCTYPE html>
<html lang="en">
<head>
<meta charset="utf-8">
<title>Brightvale Electrical</title>
<link href="https://fonts.googleapis.com/css2?family=Open+Sans:wght@400;600;700&display=swap" rel="stylesheet">
<style>
:root{
  --red:#e3202a;
  --dark:#2d2d2d;
  --darker:#1b1b1b;
  --nav:#222;
  --grey:#f1f1f1;
  --form:#e4e4e4;
  --text:#555;
  --muted:#999;
  --white:#fff;
}
*{box-sizing:border-box;margin:0;padding:0}
html,body{width:745px;height:1200px;overflow:hidden}
body{font-family:'Open Sans',Arial,sans-serif;color:var(--text);background:var(--white);position:relative;font-size:7px}
.site-header{position:absolute;top:0;left:0;width:745px;height:44px;background:var(--white);display:flex;align-items:center;padding:0 40px}
.brand{display:flex;align-items:center;gap:6px}
.brand-mark{width:16px;height:16px;background:var(--red)}
.brand-name{font-weight:700;font-size:17px;color:var(--darker)}
.brand-tag{font-size:5px;color:var(--muted);margin-top:1px}
.header-contact{margin-left:auto;display:flex;align-items:center;gap:10px;font-size:7px}
.header-contact .phone{color:var(--red);font-weight:700;font-size:9px}
.social-squares{display:flex;gap:3px}
.social-squares span{width:11px;height:11px;background:#2f5ea8;display:block}
.main-nav{position:absolute;top:44px;left:0;width:745px;height:18px;background:var(--nav);display:flex;padding-left:40px}
.main-nav a{color:var(--white);font-size:6.5px;text-decoration:none;padding:0 12px;line-height:18px}
.main-nav a.active{background:var(--red)}
.hero{position:absolute;top:62px;left:0;width:745px;height:286px;background:linear-gradient(180deg,#b8c6d3 0%,#9aa5ad 45%,#6b6d6e 70%,#4b4c4c 100%)}
.hero-banner{position:absolute;left:462px;top:52px;width:178px;background:var(--red);color:var(--white);font-weight:700;font-size:15px;text-align:center;padding:7px 4px;line-height:1.35}
.hero-dots{position:absolute;left:360px;top:268px;display:flex;gap:4px}
.hero-dots span{width:5px;height:5px;border-radius:50%;background:var(--white)}
.hero-dots span.on{background:var(--red)}
.welcome{position:absolute;top:348px;left:0;width:745px;height:122px;background:var(--dark);padding:32px 40px}
.welcome h1{color:var(--white);font-size:14px;font-weight:600}
.welcome h1 .hl{color:var(--red);font-weight:700}
.welcome h1 small{font-size:10px;font-weight:600}
.welcome p{color:#aaa;font-size:6px;width:300px;margin-top:8px;line-height:1.5}
.welcome-art{position:absolute;left:560px;top:20px;width:140px;height:84px;background:radial-gradient(circle,#6a6a6a 0%,#3a3a3a 70%,var(--dark) 100%)}
.section-title{color:var(--red);font-size:15px;font-weight:700;text-align:center}
.section-intro{font-size:6px;text-align:center;width:520px;margin:6px auto 0;line-height:1.5}
.projects{position:absolute;top:470px;left:0;width:745px;height:200px;padding-top:16px}
.project-grid{display:flex;gap:12px;justify-content:center;margin-top:16px}
.project-card{width:140px;height:104px;border:1px solid #ddd;display:flex;background:var(--white)}
.project-card.featured{border:2px solid var(--red)}
.project-text{width:50%;padding:8px 5px}
.project-text h3{color:var(--red);font-size:6.5px;font-weight:700;line-height:1.3}
.project-text p{font-size:4.5px;line-height:1.4;margin-top:3px}
.btn-small{display:inline-block;background:var(--red);color:var(--white);font-size:4.5px;padding:3px 6px;margin-top:10px}
.project-photo{width:50%;background:linear-gradient(160deg,#8a8f94,#4d5257)}
.capabilities{position:absolute;top:670px;left:0;width:745px;height:285px;background:var(--grey);padding-top:14px}
.cap-grid{display:flex;gap:26px;justify-content:center;margin-top:12px}
.cap-col{width:268px}
.cap-photo{height:116px;background:linear-gradient(180deg,#a9bccc 0%,#c9c6c0 55%,#7c7a76 100%)}
.cap-col h3{font-size:8px;font-weight:700;color:var(--darker);margin-top:8px}
.cap-list{display:grid;grid-template-columns:1fr 1fr;gap:3px 8px;margin-top:6px;list-style:none}
.cap-list li{font-size:5px;display:flex;align-items:center;gap:3px;padding:1px 2px}
.cap-list li::before{content:"";width:3px;height:3px;background:var(--red);display:block}
.cap-list li.on{background:var(--red);color:var(--white)}
.cap-list li.on::before{background:var(--white)}
.contact{position:absolute;top:955px;left:0;width:745px;height:137px;background:var(--form);padding:12px 40px}
.contact h2{color:var(--red);font-size:11px;font-weight:700}
.form-row{display:flex;gap:8px;margin-top:8px}
.field{flex:1;height:13px;background:var(--white);border:1px solid #ccc;font-size:5px;color:var(--muted);padding:3px 4px}
.btn-red{width:120px;background:var(--red);color:var(--white);font-size:6px;font-weight:700;text-align:center;display:flex;align-items:center;justify-content:center}
.field.message{height:30px}
.site-footer{position:absolute;top:1092px;left:0;width:745px;height:108px;background:var(--darker);padding:14px 40px;display:flex;gap:40px}
.footer-col{width:140px;color:#888;font-size:5px;line-height:1.6}
.footer-col h4{color:var(--red);font-size:8px;font-weight:600;margin-bottom:6px}
.footer-col .brand-name{color:var(--white);font-size:13px}
.footer-social{display:flex;gap:4px}
.footer-social span{width:10px;height:10px;border-radius:50%;background:#2f5ea8;display:block}
.footer-bottom{position:absolute;bottom:0;left:0;width:745px;height:10px;background:#111;color:var(--red);font-size:4.5px;text-align:center;line-height:10px}
</style>
</head>
<body>
<header class="site-header">
  <div class="brand">
    <span class="brand-mark"></span>
    <div><div class="brand-name">Brightvale</div><div class="brand-tag">Electrical &amp; Communications</div></div>
  </div>
  <div class="header-contact">
    <span>info@brightvaleelectrical.com.au</span>
    <span class="phone">04 0000 1234</span>
    <div class="social-squares"><span></span><span></span><span></span></div>
  </div>
</header>
<nav class="main-nav">
  <a class="active">Home</a><a>About Us</a><a>Our Projects</a><a>Our Capabilities</a><a>Blog</a><a>Contact Us</a>
</nav>
<section class="hero" role="img" aria-label="Photo of a modern brick home with electrical installation">
  <div class="hero-banner">Development and<br>Installation</div>
  <div class="hero-dots"><span class="on"></span><span></span><span></span></div>
</section>
<section class="welcome">
  <h1>Welcome To <span class="hl">Brightvale</span> <small>Electrical &amp; Communications</small></h1>
  <p>We deliver safe, reliable electrical and communication work for homes, builders and businesses across the region. Our licensed team handles every job from first plan to final test, on time and on budget, with clear pricing and tidy results you can trust.</p>
  <div class="welcome-art" role="img" aria-label="Decorative dot pattern"></div>
</section>
<section class="projects">
  <h2 class="section-title">Our Projects</h2>
  <p class="section-intro">A selection of completed jobs, from new residential builds to large commercial fit-outs. Each project shows our care for detail, safe installation and quality finish across lighting, power and data systems.</p>
  <div class="project-grid">
    <article class="project-card featured"><div class="project-text"><h3>New Home Build Fit-out</h3><p>Full wiring and lighting for a new family home.</p><span class="btn-small">Read More</span></div><div class="project-photo" role="img" aria-label="Project photo of an office interior"></div></article>
    <article class="project-card"><div class="project-text"><h3>Office Lighting Upgrade</h3><p>LED lighting and power for a modern office.</p><span class="btn-small">Read More</span></div><div class="project-photo" role="img" aria-label="Project photo of a switchboard"></div></article>
    <article class="project-card"><div class="project-text"><h3>Switchboard Replacement</h3><p>Safe new board for a growing workshop.</p><span class="btn-small">Read More</span></div><div class="project-photo" role="img" aria-label="Project photo of a warehouse"></div></article>
    <article class="project-card"><div class="project-text"><h3>Data Cabling Install</h3><p>Network and data points for a new site.</p><span class="btn-small">Read More</span></div><div class="project-photo" role="img" aria-label="Project photo of a kitchen"></div></article>
  </div>
</section>
<section class="capabilities">
  <h2 class="section-title">Our Capabilities</h2>
  <p class="section-intro">We offer a full range of electrical and communication services for residential and commercial clients, backed by licensed staff, modern tools and a strong focus on safety and quality.</p>
  <div class="cap-grid">
    <div class="cap-col">
      <div class="cap-photo" role="img" aria-label="Photo of modern townhouses"></div>
      <h3>Residential Capability Statement</h3>
      <ul class="cap-list"><li class="on">New Homes Wiring</li><li>Ceiling Fans</li><li>Switchboard Upgrades</li><li>Smoke Alarms</li><li>LED Lighting Installation</li><li>Kitchen / Bathroom Projects</li></ul>
    </div>
    <div class="cap-col">
      <div class="cap-photo" role="img" aria-label="Photo of a commercial concrete building"></div>
      <h3>Commercial / Industrial Capability Statement</h3>
      <ul class="cap-list"><li class="on">Office Fit-outs</li><li>Phone/Data Points</li><li>Lighting Design</li><li>Power Solutions</li><li>Emergency and Exit Lighting</li><li>Data Networking</li></ul>
    </div>
  </div>
</section>
<section class="contact">
  <h2>Contact From</h2>
  <div class="form-row"><div class="field">Enter Your Name</div><div class="field">Enter Your Phone</div><div class="field">Enter Your Email</div><div class="btn-red">Upload File</div></div>
  <div class="form-row"><div class="field message">Message</div><div class="btn-red">SUBMIT</div></div>
</section>
<footer class="site-footer">
  <div class="footer-col">
    <div class="brand-name">Brightvale</div>
    <p>Licensed electrical contractors serving homes, builders and businesses. We do not disclose information to third parties.</p>
  </div>
  <div class="footer-col"><h4>Follow Us On</h4><div class="footer-social"><span></span><span></span><span></span></div></div>
  <div class="footer-col"><h4>Location</h4><p>PO Box 120 Brightvale<br>Hillside QLD 4000</p></div>
  <div class="footer-col"><h4>Contact Info</h4><p>04 0000 1234<br>07 0000 5678<br>info@brightvaleelectrical.com.au</p></div>
  <div class="footer-bottom">© Brightvale Electrical &amp; Communications. All rights reserved.</div>
</footer>
</body>
</html>
```